Harborline Claims Advocates Business card

We need to get business card Design for our Company we are Public Adjusters in Chicago Illinois - i like to see good combination and elements from my Company Logo. as well To be an two side design
Updates

Target Market(s)

Home /Business owner Property Managers

Industry/Entity Type

Business

Contact Information for Business Card

to show the Element of our logo i will Like 3D

Font styles to use
Sans Serif

Requirements
Must have
• Logo and Element of the Logo in 3D
Nice to have
• Logo That we Provide 3D Same Colors or open for suggestions
Should not have
• unleare view -

```html
<!DOCTYPE html>
<html lang="en">
<head>
<meta charset="utf-8">
<title>Harborline Claims Advocates – Business Card</title>
<link rel="stylesheet" href="https://fonts.googleapis.com/css2?family=Open+Sans:wght@400;600;700&display=swap">
<style>
  :root {
    --bg: #e9e6e1;
    --white: #ffffff;
    --navy: #0e1763;
    --navy-deep: #0a0f45;
    --blue: #1c3ec4;
    --blue-bright: #2b55e6;
    --accent: #e4572e;
    --text-grey: #5a5a5a;
    --line-light: rgba(255,255,255,0.35);
  }
  * { margin: 0; padding: 0; box-sizing: border-box; }
  html, body { width: 1200px; height: 795px; overflow: hidden; }
  body {
    background: var(--bg);
    font-family: "Open Sans", Arial, sans-serif;
    display: flex;
    align-items: center;
    justify-content: center;
    gap: 60px;
  }
  .card {
    width: 520px;
    height: 298px;
    position: relative;
    overflow: hidden;
  }
  .brand-dot {
    flex: 0 0 auto;
    width: 26px; height: 26px; border-radius: 50%;
    background: var(--blue);
  }
  .brand-name {
    color: var(--blue);
    font-weight: 700;
    font-size: 15px;
    white-space: nowrap;
  }

  /* Front */
  .card-front {
    background: var(--white);
    box-shadow: 0 2px 10px rgba(0,0,0,0.15);
  }
  .front-brand {
    position: absolute;
    left: 30px; top: 30px;
    display: flex; align-items: center; gap: 10px;
  }
  .person {
    position: absolute;
    right: 30px; top: 30px;
    text-align: right;
  }
  .person-name {
    color: var(--blue);
    font-size: 17px;
    font-weight: 600;
    letter-spacing: 0.5px;
  }
  .person-title {
    color: var(--accent);
    font-size: 11px;
    margin-top: 2px;
  }
  .address {
    position: absolute;
    right: 30px; top: 96px;
    text-align: right;
    color: var(--text-grey);
    font-size: 11.5px;
    line-height: 1.55;
  }
  .divider {
    position: absolute;
    left: 30px; right: 30px; top: 172px;
    height: 1px;
    background: var(--accent);
  }
  .contacts {
    position: absolute;
    left: 30px; top: 186px;
    list-style: none;
    color: var(--text-grey);
    font-size: 11.5px;
    line-height: 1.6;
  }
  .contacts li { display: flex; align-items: center; gap: 8px; }
  .contacts svg { width: 11px; height: 11px; fill: var(--blue); flex: 0 0 auto; }
  .edge-band {
    position: absolute; left: 0; right: 0; bottom: 0; height: 8px;
    background: linear-gradient(90deg, var(--accent) 0 35%, var(--blue) 35% 100%);
  }

  /* Back */
  .card-back {
    background: radial-gradient(circle at 50% 50%, var(--blue-bright) 0%, var(--blue) 30%, var(--navy) 70%, var(--navy-deep) 100%);
    box-shadow: 0 2px 10px rgba(0,0,0,0.25);
  }
  .back-brand {
    position: absolute;
    left: 50%; top: 44%;
    transform: translate(-50%, -50%);
    display: flex; align-items: center; gap: 12px;
  }
  .back-brand .brand-dot { background: var(--accent); width: 30px; height: 30px; }
  .back-brand .brand-name { color: var(--white); font-size: 19px; }
  .back-rule {
    position: absolute;
    left: 60px; right: 60px; top: 196px;
    height: 1px;
    background: var(--line-light);
  }
  .back-web {
    position: absolute;
    left: 0; right: 0; top: 214px;
    text-align: center;
    color: rgba(255,255,255,0.75);
    font-size: 11.5px;
    letter-spacing: 1.5px;
  }
</style>
</head>
<body>
  <section class="card card-front">
    <div class="front-brand">
      <span class="brand-dot"></span>
      <span class="brand-name">Harborline Claims Advocates</span>
    </div>
    <div class="person">
      <div class="person-name">DANIEL REYES</div>
      <div class="person-title">CEO/Founder</div>
    </div>
    <div class="address">
      4120 Larkspur Court<br>
      Juneau, Alaska 34810<br>
      www.harborlineclaims.com
    </div>
    <div class="divider"></div>
    <ul class="contacts">
      <li><svg viewBox="0 0 24 24"><path d="M6.6 10.8a15.1 15.1 0 0 0 6.6 6.6l2.2-2.2c.3-.3.7-.4 1-.2 1.1.4 2.3.6 3.6.6.6 0 1 .4 1 1V20c0 .6-.4 1-1 1A17 17 0 0 1 3 4c0-.6.4-1 1-1h3.5c.6 0 1 .4 1 1 0 1.3.2 2.5.6 3.6.1.3 0 .7-.2 1z"/></svg>555 204 1836</li>
      <li><svg viewBox="0 0 24 24"><path d="M7 2h10a2 2 0 0 1 2 2v16a2 2 0 0 1-2 2H7a2 2 0 0 1-2-2V4a2 2 0 0 1 2-2zm0 3v13h10V5z"/></svg>555 318 7720</li>
      <li><svg viewBox="0 0 24 24"><path d="M6 3h12v5H6zM4 9h16a2 2 0 0 1 2 2v6h-4v4H6v-4H2v-6a2 2 0 0 1 2-2zm4 7v3h8v-3z"/></svg>555 642 0915</li>
      <li><svg viewBox="0 0 24 24"><path d="M3 5h18v14H3zm2 2v.5l7 4.5 7-4.5V7z"/></svg>hello@harborlineclaims.com</li>
    </ul>
    <div class="edge-band"></div>
  </section>

  <section class="card card-back">
    <div class="back-brand">
      <span class="brand-dot"></span>
      <span class="brand-name">Harborline Claims Advocates</span>
    </div>
    <div class="back-rule"></div>
    <div class="back-web">www.HarborlineClaimsAdvocates.com</div>
  </section>
</body>
</html>
```